Property Services Company Needs a Brochure Design

Looking for a new brochure design for an existing property services company.

We provide a range of property services from, market research, real estate brokerage, valuation and appraisal, property development and other real estate consulting services.

We would like a fresh modern brochure design with good graphics and features. Our colours are white, blue and orange.

The design should communicate, attention to detail, superior service delivery and distinction in results.
Updates

I would like the brochure to be roughly about 20 pages.

Containing the following,

1) An introduction
2) Contents Page
2) What we do
3) Our Services
4) Agency & Brokerage
5) Real Estate Consulting
6) Market Research
7) Appraisal & Valuation
8) Project Management
9) Property Development

I would also like icons to represent items 4,5,6,7,8 & 9, they should be represented vertically on each of the pages from the contents page and highlighted individually on the pages that they represent.. i.e. on appraisal & valuation page, all six icons will be arranged vertically and the appraisal and valuations icon will be highlighted.

I will also like to have images that depict the services on the various pages.

I have some pages I think will flow which I will upload shortly.

Industry/Entity Type

Real Estate

Font styles to use
Serif

Colors
f78f20
0455a3

```html
<!DOCTYPE html>
<html lang="en">
<head>
<meta charset="utf-8">
<title>Calverd Brochure – Pages 3 to 6</title>
<link rel="stylesheet" href="https://fonts.googleapis.com/css2?family=Open+Sans:wght@400;600;700&family=Noto+Serif:ital@1&display=swap">
<style>
  :root {
    --stage: #2b2b2b;
    --blue: #0455a3;
    --navy: #0b3a78;
    --orange: #f78f20;
    --orange-deep: #d9791a;
    --ink: #111;
    --body-ink: #454545;
    --menu-ink: #f6dcbc;
    --page-white: #ffffff;
    --page-shade: #cfcfcf;
  }
  * { box-sizing: border-box; margin: 0; padding: 0; }
  html, body { width: 1200px; height: 900px; overflow: hidden; }
  body {
    position: relative;
    background: var(--stage);
    font-family: "Open Sans", Arial, sans-serif;
  }
  .spread-label {
    position: absolute;
    left: 0; width: 1200px;
    text-align: center;
    color: #fff;
    font-family: "Noto Serif", Georgia, serif;
    font-style: italic;
    font-size: 21px;
  }
  .spread {
    position: absolute;
    overflow: hidden;
    background: radial-gradient(ellipse at 35% 35%, var(--page-white) 30%, var(--page-shade) 100%);
    box-shadow: 0 4px 10px rgba(0,0,0,.6);
  }
  .spread-shapes { position: absolute; left: 0; top: 0; }
  .page-heading {
    position: absolute;
    font-size: 9px;
    font-weight: 700;
    color: var(--ink);
    letter-spacing: .2px;
  }
  .body-copy {
    position: absolute;
    width: 388px;
    font-size: 9.2px;
    line-height: 11.2px;
    color: var(--body-ink);
  }
  .body-copy p + p { margin-top: 11px; }

  /* Pages 3–4 */
  .spread--intro { left: 133px; top: 67px; width: 924px; height: 326px; }
  .contents-list { list-style: none; }
  .contents-item {
    position: absolute;
    right: 26px;
    font-size: 11.2px;
    font-weight: 700;
    color: var(--menu-ink);
  }

  /* Pages 5–6 */
  .spread--services { left: 133px; top: 473px; width: 929px; height: 327px; }
  .service-name {
    position: absolute;
    font-size: 16px;
    font-weight: 700;
    white-space: nowrap;
  }
  .service-name--blue { color: var(--blue); left: 531px; }
  .service-name--orange { color: var(--orange-deep); right: 79px; }
  .service-icon { position: absolute; }
</style>
</head>
<body>

<div class="spread-label" style="top:18px;">page 3-4</div>

<section class="spread spread--intro">
  <svg class="spread-shapes" width="924" height="326" viewBox="0 0 924 326">
    <rect x="0" y="0" width="22" height="326" fill="var(--navy)"/>
    <rect x="22" y="0" width="5" height="326" fill="var(--orange)"/>
    <rect x="463" y="0" width="461" height="326" fill="#f2f2f2"/>
    <polygon points="263,326 463,326 463,126" fill="var(--navy)"/>
    <polygon points="463,0 497,0 543,46 463,126" fill="var(--navy)"/>
    <polygon points="557,51 924,51 924,258 753,258" fill="var(--orange-deep)"/>
    <g role="img" aria-label="Photo of a smiling businessman in a suit reading a newspaper on a sofa">
      <defs>
        <linearGradient id="photoTone" x1="0" y1="0" x2="1" y2="1">
          <stop offset="0" stop-color="#d9d6cf"/>
          <stop offset=".55" stop-color="#8a8c92"/>
          <stop offset="1" stop-color="#3b3f4a"/>
        </linearGradient>
      </defs>
      <polygon points="486,103 607,103 753,258 753,326 463,326 463,126" fill="url(#photoTone)"/>
    </g>
    <polygon points="753,258 800,258 868,326 753,326" fill="var(--navy)"/>
    <line x1="800" y1="258" x2="868" y2="326" stroke="var(--orange)" stroke-width="4"/>
    <line x1="263" y1="326" x2="545" y2="44" stroke="var(--orange)" stroke-width="6"/>
    <line x1="497" y1="0" x2="560" y2="54" stroke="var(--orange)" stroke-width="5"/>
    <g stroke="#f3c89a" stroke-width="1" opacity=".8">
      <line x1="583" y1="78" x2="898" y2="78"/>
      <line x1="606" y1="103" x2="898" y2="103"/>
      <line x1="631" y1="129" x2="898" y2="129"/>
      <line x1="655" y1="155" x2="898" y2="155"/>
      <line x1="679" y1="180" x2="898" y2="180"/>
      <line x1="704" y1="206" x2="898" y2="206"/>
      <line x1="728" y1="232" x2="898" y2="232"/>
    </g>
  </svg>

  <h2 class="page-heading" style="left:50px; top:15px;">INTRODUCTION</h2>
  <div class="body-copy" style="left:47px; top:55px;">
    <p>CALVERD was incorporated in 1984 as an interior design and property development company. Over the years we have expanded our service with a foundation based on core strengths, unrivalled local expertise, network and knowledge combined with strategic partnerships.</p>
    <p>Calverd offers a comprehensive range of services on a local, regional, national and international basis to tenants, owners, and investors within the residential and commercial property market.</p>
    <p>Our clients depend on our ability to draw on years of experience in the local market, our professionals know their communities and the property market inside and out, and provide knowledgeable, creative solutions to all their real estate needs.</p>
    <p style="width:300px;">We currently provide services to corporations, financial institutions, government agencies, public sector entities, developers and investors. Our knowledge, expertise, experience and technological resources allow us to be a superior service provider.</p>
  </div>

  <h2 class="page-heading" style="right:41px; top:15px;">CONTENT</h2>
  <ul class="contents-list">
    <li class="contents-item" style="top:59px;">What we do</li>
    <li class="contents-item" style="top:85px;">Our Services</li>
    <li class="contents-item" style="top:111px;">Agency &amp; Brokerage</li>
    <li class="contents-item" style="top:136px;">Real Estate Consulting</li>
    <li class="contents-item" style="top:162px;">Market Research</li>
    <li class="contents-item" style="top:187px;">Appraisal &amp; Valuation</li>
    <li class="contents-item" style="top:213px;">Project Management</li>
    <li class="contents-item" style="top:238px;">Property Development</li>
  </ul>
</section>

<div class="spread-label" style="top:432px;">page 5-6</div>

<section class="spread spread--services">
  <svg class="spread-shapes" width="929" height="327" viewBox="0 0 929 327">
    <rect x="0" y="0" width="24" height="327" fill="var(--navy)"/>
    <rect x="24" y="0" width="6" height="327" fill="var(--orange)"/>
    <rect x="465" y="295" width="464" height="5" fill="var(--orange)"/>
    <rect x="465" y="300" width="464" height="27" fill="var(--navy)"/>
  </svg>

  <h2 class="page-heading" style="left:50px; top:16px;">WHAT WE DO</h2>
  <div class="body-copy" style="left:47px; top:42px;">
    <p>Calverd is a leading property services company, incorporated in 1984, providing bespoke solutions in advisory, brokerage and turnkey solutions to owners, occupiers and property investors. Over the years we have expanded our services with a foundation based on core strengths, unrivalled local expertise, network and knowledge combined with strategic partnership. As well as providing property solutions we also develop commercial and residential units.</p>
    <p>Our growth has been based on maintaining relationships with our extensive client base, ranging from financial institutions, government agencies, airlines and servicing companies, manufacturing companies, multinationals and local corporations, to private developers and investors. Our clients depend on our ability to draw on years of experience in the local market, our professionals know their communities and the property market inside and out, and provide knowledgeable, creative solutions to all their real estate needs.</p>
    <p>The combination of our integrated services allows us to provide a superior end to end solution to our clients, customized to their own requirements. Market research is a core component to our business model, allowing us to make informed decisions based based on research findings. Our brokerage team also benefits from this information, allowing our associates to advise clients on how best to maximise return on their investment on the sale or buy side within a short timeline.</p>
    <p>We pay great attention to detail in consideration of our client requirements, delivering mandates with distinction.</p>
  </div>

  <h2 class="page-heading" style="right:21px; top:16px;">OUR SERVICES</h2>

  <svg class="service-icon" style="left:479px; top:40px;" width="40" height="48" viewBox="0 0 40 48" aria-hidden="true">
    <g fill="var(--orange-deep)">
      <rect x="2" y="32" width="6" height="14"/>
      <rect x="11" y="27" width="6" height="19"/>
      <rect x="20" y="22" width="6" height="24"/>
      <rect x="29" y="16" width="6" height="30"/>
      <polygon points="37,2 28,3 31,6 19,17 12,12 1,22 3,24 12,16 19,21 33,8 36,11"/>
    </g>
  </svg>
  <div class="service-name service-name--blue" style="top:62px;">Agency &amp; Brokerage</div>

  <div class="service-name service-name--orange" style="top:101px;">Appraisal &amp; Valuation</div>
  <svg class="service-icon" style="left:866px; top:94px;" width="42" height="36" viewBox="0 0 42 36" aria-hidden="true">
    <g fill="none" stroke="var(--navy)" stroke-width="2">
      <line x1="21" y1="3" x2="21" y2="31"/>
      <line x1="5" y1="8" x2="37" y2="8"/>
      <polyline points="8,8 2,22"/><polyline points="8,8 14,22"/>
      <polyline points="34,8 28,22"/><polyline points="34,8 40,22"/>
    </g>
    <g fill="var(--navy)">
      <path d="M1,22 h14 a7,5 0 0 1 -14,0z"/>
      <path d="M27,22 h14 a7,5 0 0 1 -14,0z"/>
      <rect x="13" y="31" width="16" height="3"/>
      <circle cx="21" cy="4" r="2.5"/>
    </g>
  </svg>

  <svg class="service-icon" style="left:480px; top:131px;" width="44" height="42" viewBox="0 0 44 42" aria-hidden="true">
    <circle cx="17" cy="17" r="14" fill="none" stroke="var(--orange-deep)" stroke-width="4"/>
    <line x1="27" y1="27" x2="40" y2="39" stroke="var(--orange-deep)" stroke-width="6" stroke-linecap="round"/>
    <polygon points="17,9 9,16 11,16 11,24 23,24 23,16 25,16" fill="var(--orange-deep)"/>
  </svg>
  <div class="service-name service-name--blue" style="top:140px;">Real Estate Consulting</div>

  <div class="service-name service-name--orange" style="top:179px;">Project Management</div>
  <svg class="service-icon" style="left:868px; top:170px;" width="39" height="39" viewBox="0 0 39 39" aria-hidden="true">
    <rect x="0" y="0" width="39" height="39" rx="5" fill="var(--navy)"/>
    <g fill="none" stroke="#fff" stroke-width="2.6">
      <path d="M10,17 a10,10 0 0 1 18,-4"/>
      <path d="M29,22 a10,10 0 0 1 -18,4"/>
    </g>
    <polygon points="30,7 30,15 23,14" fill="#fff"/>
    <polygon points="9,32 9,24 16,25" fill="#fff"/>
  </svg>

  <svg class="service-icon" style="left:480px; top:212px;" width="38" height="40" viewBox="0 0 38 40" aria-hidden="true">
    <g fill="var(--orange-deep)">
      <circle cx="7" cy="6" r="4"/><circle cx="31" cy="6" r="4"/><circle cx="19" cy="16" r="4.5"/>
      <rect x="2" y="11" width="10" height="14" rx="3"/>
      <rect x="26" y="11" width="10" height="14" rx="3"/>
      <rect x="13" y="22" width="12" height="17" rx="3"/>
    </g>
  </svg>
  <div class="service-name service-name--blue" style="top:218px;">Market Research</div>

  <div class="service-name service-name--orange" style="top:257px;">Property Development</div>
  <svg class="service-icon" style="left:866px; top:245px;" width="46" height="32" viewBox="0 0 46 32" aria-hidden="true">
    <g fill="var(--navy)">
      <rect x="0" y="20" width="8" height="12" rx="1.5"/>
      <rect x="12" y="14" width="8" height="18" rx="1.5"/>
      <rect x="24" y="7" width="8" height="25" rx="1.5"/>
      <rect x="36" y="0" width="8" height="32" rx="1.5"/>
    </g>
  </svg>
</section>

</body>
</html>
```